A specialised Sport management needs a corporate brochure design

We are a specialized company in the management and consultancy of sports events. and need to have a company brochure
We provide the following services;
Event management
Venues management
Production
Ticketing
Consulting
Hospitality
Activity management
Event timing
Branding of event
Event supplies
We need a corporate profile design for our company to showcase the major events that we have covered , with images, information, statistics, surveys, products and services used. We want to highlight our professionalism and execution of the events, experience of the participants, spectators . How we have grown in the past few years and reached the international standards.
Objectives of the work:
To get sponsors and partners for future business and to present Tri-Crest
as not just a sports management company but also a professional sports
events management company.
You can check our website
www.tri-crest.example
Target Market(s)
Sponsors and corporate partners
Industry/Entity Type
Events
Requirements
Must have
- Must Have:
- - Very professional look
- -Some event images,Event information, statistics, surveys, products and services used. We want to highlight our professionalism and execution of the events (Attached)
Nice to have
- Similar momentom of the below design
- http://www.lumavent.example/wp-content/themes/lumavent/pdf/CP-2014-15-V10-Web.pdf

```html
<!DOCTYPE html>
<html lang="en">
<head>
<meta charset="utf-8">
<title>Tri-Crest Partnership Brochure – Benefits &amp; Events Calendar 2015</title>
<link rel="stylesheet" href="https://fonts.googleapis.com/css2?family=Orbitron:wght@600;700&family=Roboto:wght@400;700&display=swap">
<style>
  :root {
    --bg: #dcdcdc;
    --paper: #efede9;
    --orange: #f15a29;
    --orange-deep: #e0391b;
    --orange-light: #f47a45;
    --ink: #2b2b2b;
    --grey-band: #6f6f71;
    --grey-bar: #8a8a8c;
    --cell: #ffffff;
    --tab-green: #2e8b3a;
    --photo-sky: #dfe6ec;
    --photo-sand: #d9c3a0;
  }
  * { box-sizing: border-box; margin: 0; padding: 0; }
  html, body { width: 1200px; height: 799px; overflow: hidden; }
  body { background: var(--bg); font-family: "Roboto", Arial, sans-serif; color: var(--ink); position: relative; }

  .spread {
    position: absolute; left: 40px; top: 200px; width: 1120px; height: 400px;
    display: flex; box-shadow: 0 6px 18px rgba(0,0,0,.18);
  }
  .page { position: relative; width: 560px; height: 400px; background: var(--paper); overflow: hidden; }
  .page--left { background: linear-gradient(90deg, var(--paper) 85%, #e3e1dc); }
  .page--right { background: linear-gradient(90deg, #e3e1dc, var(--paper) 12%); }

  .page-tab { position: absolute; width: 16px; height: 7px; background: var(--tab-green); }
  .page--left .page-tab { left: 0; top: 236px; }
  .page--right .page-tab { right: 0; top: 118px; }

  /* Left page */
  .hero-photo {
    position: absolute; right: 0; top: 0; width: 300px; height: 250px;
    background:
      linear-gradient(90deg, var(--paper) 0%, rgba(239,237,233,0) 35%),
      linear-gradient(180deg, var(--photo-sky) 0%, #e8dfcf 45%, var(--photo-sand) 100%);
  }
  .benefits-title {
    position: absolute; left: 40px; top: 92px;
    font-family: "Orbitron", sans-serif; font-weight: 700; font-size: 40px;
    letter-spacing: 1px; color: var(--orange); line-height: 48px;
  }
  .benefit-group { position: absolute; left: 40px; }
  .benefit-group--partner { top: 150px; width: 330px; }
  .benefit-group--why { top: 314px; width: 440px; }
  .benefit-group h3 { font-size: 11px; font-weight: 700; line-height: 14px; margin-bottom: 1px; }
  .bullet-list { list-style: none; font-size: 10px; line-height: 13px; }
  .bullet-list li { white-space: nowrap; }
  .bullet-list li::before { content: "•"; color: var(--orange); margin-right: 5px; }

  .terms-band { position: absolute; right: 0; top: 250px; width: 200px; height: 58px; }
  .terms-band svg { position: absolute; inset: 0; width: 100%; height: 100%; }
  .terms-text { position: absolute; left: 22px; top: 8px; color: #fff; }
  .terms-text h4 { font-size: 10px; font-weight: 700; margin-bottom: 2px; }
  .terms-text .bullet-list { font-size: 8.5px; line-height: 11px; }
  .terms-text .bullet-list li::before { color: #fff; }

  /* Right page */
  .accent-stripes { position: absolute; left: 30px; top: 0; width: 110px; height: 210px; }
  .calendar-title {
    position: absolute; right: 40px; top: 44px; text-align: right;
    font-family: "Orbitron", sans-serif; font-weight: 700; font-size: 28px;
    line-height: 30px; color: var(--orange); letter-spacing: 1px;
  }
  .corner-swoosh { position: absolute; right: 0; bottom: 0; width: 380px; height: 190px; }

  .month-block { position: absolute; display: flex; }
  .month { display: flex; flex-direction: column; }
  .month-name { font-size: 13px; color: var(--orange); padding-left: 12px; height: 16px; line-height: 16px; }
  .month-cells { display: flex; }
  .event { width: 50px; display: flex; flex-direction: column; }
  .event--wide { width: 64px; }
  .event-date {
    height: 10px; background: var(--grey-bar); color: #fff; font-size: 6px;
    line-height: 10px; text-align: center; white-space: nowrap;
  }
  .event-date--tall { height: 18px; line-height: 8px; padding-top: 1px; }
  .event-brand {
    height: 28px; background: var(--cell); border-right: 1px solid #e2e2e2;
    display: flex; align-items: center; justify-content: center; gap: 3px;
    font-size: 6.5px; font-weight: 700; color: var(--ink); text-align: center; line-height: 8px;
  }
  .brand-dot { width: 5px; height: 5px; border-radius: 50%; background: var(--orange); flex: none; }

  .row-one { left: 142px; top: 140px; }
  .row-two { left: 420px; top: 200px; }
  .row-three { left: 110px; top: 262px; }
</style>
</head>
<body>
  <main class="spread">
    <section class="page page--left">
      <div class="hero-photo" role="img" aria-label="Photo of a trail runner in a green shirt racing through desert rocks"></div>
      <span class="page-tab"></span>

      <h1 class="benefits-title">BENEFITS</h1>

      <div class="benefit-group benefit-group--partner">
        <h3>Partner's Benefits</h3>
        <ul class="bullet-list">
          <li>Featured in all Tri-Crest Marketing</li>
          <li>Logo placement on our Website</li>
          <li>Branding on event location as Event Partner</li>
          <li>Free booth on location at our events (minimum 3 of our events)</li>
          <li>Email advertisement</li>
          <li>Featured in our bi-annual newsletter</li>
          <li>Exposure at our partnered event outlets</li>
        </ul>
      </div>

      <div class="benefit-group benefit-group--why">
        <h3>Why Partner with Us?</h3>
        <ul class="bullet-list">
          <li>Be part of the fastest growing Events in terms of Participation and Exposure</li>
          <li>Be part of the most exciting Sport Events in Kuwait</li>
          <li>High Interaction with Participants and Spectators</li>
          <li>Year long Exposure through our Events and Activities</li>
        </ul>
      </div>

      <div class="terms-band">
        <svg viewBox="0 0 200 58" preserveAspectRatio="none">
          <polygon points="14,0 200,0 200,58 0,58" fill="var(--grey-band)"/>
          <polyline points="14,0 0,58" stroke="var(--orange)" stroke-width="3" fill="none"/>
        </svg>
        <div class="terms-text">
          <h4>Partnership terms</h4>
          <ul class="bullet-list">
            <li>Exclusivity</li>
            <li>Support in Marketing our events through:<br>&nbsp;&nbsp;&nbsp;Social Media, Database, On Location</li>
          </ul>
        </div>
      </div>
    </section>

    <section class="page page--right">
      <svg class="accent-stripes" viewBox="0 0 110 210">
        <polygon points="30,0 58,0 30,210 8,210" fill="var(--orange)"/>
        <polygon points="66,0 78,0 46,210 38,210" fill="var(--orange-light)"/>
        <polygon points="88,0 96,0 66,150 60,150" fill="var(--orange)"/>
      </svg>
      <span class="page-tab"></span>

      <h2 class="calendar-title">EVENTS<br>CALENDAR<br>2015</h2>

      <svg class="corner-swoosh" viewBox="0 0 380 190" preserveAspectRatio="none">
        <polygon points="380,50 380,190 20,190 120,150 300,110" fill="var(--orange-light)"/>
        <polygon points="380,80 380,190 60,190 320,120" fill="var(--orange-deep)"/>
      </svg>

      <div class="month-block row-one">
        <div class="month">
          <span class="month-name">Jan</span>
          <div class="month-cells">
            <div class="event"><span class="event-date">7th - 10th</span><span class="event-brand">Dune Run</span></div>
            <div class="event"><span class="event-date">14th - 17th</span><span class="event-brand">Sea Dash</span></div>
          </div>
        </div>
        <div class="month">
          <span class="month-name">Feb</span>
          <div class="month-cells">
            <div class="event"><span class="event-date">7th</span><span class="event-brand"><i class="brand-dot"></i>Ridgeline</span></div>
          </div>
        </div>
        <div class="month">
          <span class="month-name">Mar</span>
          <div class="month-cells">
            <div class="event"><span class="event-date">13th &amp; 14th</span><span class="event-brand">Apex Karting</span></div>
          </div>
        </div>
        <div class="month">
          <span class="month-name">Apr</span>
          <div class="month-cells">
            <div class="event"><span class="event-date">3rd &amp; 4th</span><span class="event-brand">Fun Run</span></div>
          </div>
        </div>
        <div class="month">
          <span class="month-name">Jun</span>
          <div class="month-cells">
            <div class="event"><span class="event-date">15th - 20th</span><span class="event-brand">Kids Fest</span></div>
          </div>
        </div>
        <div class="month">
          <span class="month-name">Jul</span>
          <div class="month-cells">
            <div class="event event--wide"><span class="event-date">18th Jun - 9th Jul</span><span class="event-brand">Summer Camp</span></div>
          </div>
        </div>
      </div>

      <div class="month-block row-two">
        <div class="month">
          <span class="month-name">Dec</span>
          <div class="month-cells">
            <div class="event"><span class="event-date event-date--tall">5th</span><span class="event-brand">Ember</span></div>
            <div class="event event--wide"><span class="event-date event-date--tall">10th - 12th<br>(24 Hr Karting)</span><span class="event-brand">Apex Karting</span></div>
          </div>
        </div>
      </div>

      <div class="month-block row-three">
        <div class="month">
          <span class="month-name">Oct</span>
          <div class="month-cells">
            <div class="event"><span class="event-date">24th</span><span class="event-brand">Ember</span></div>
            <div class="event"><span class="event-date">31st</span><span class="event-brand">Desert Night</span></div>
          </div>
        </div>
        <div class="month">
          <span class="month-name">Nov</span>
          <div class="month-cells">
            <div class="event"><span class="event-date">7th</span><span class="event-brand">Wing Ride</span></div>
            <div class="event"><span class="event-date">14th</span><span class="event-brand"><i class="brand-dot"></i>Trail Team</span></div>
            <div class="event"><span class="event-date">27th</span><span class="event-brand">Volt Rush</span></div>
          </div>
        </div>
      </div>
    </section>
  </main>
</body>
</html>
```